Letter design, envelope design, and more

Hello, we the Tavrin Gmbh are looking for our shop. Letter C5. Design does not have to be like a business card, so it can have straight lines. Only the color is important. The logo is the text under TaVRin omit.It should not be playful but Profesionel

Font styles to use
Sans Serif

Colors
0555a3
3176b5
85abd2
85cae6
34a7d8
0792cd
cee9f5
cfdfed
000000

Requirements
Must have
• Color like business card, Please, with the text under TaVRin, Correct address Lindmattstr. 4 Zip code 9517 Rosswil, as well as Couvert Without addressing only design and logo with TaVrn
Nice to have
• more writing articles
Should not have
• Not too colored, Text under TaVRin, bright colors

```html
<!DOCTYPE html>
<html lang="en">
<head>
<meta charset="utf-8">
<title>Tavrin Gmbh – Letterhead and Envelope</title>
<link href="https://fonts.googleapis.com/css2?family=Lato:wght@400;700&family=Yellowtail&display=swap" rel="stylesheet">
<style>
  :root {
    --backdrop: #c9cacc;
    --navy: #23256b;
    --steel: #7e9bb4;
    --steel-line: #8aa3bb;
    --body-text: #55565a;
    --paper: #ffffff;
    --paper-shade: #e3e3e7;
  }
  * { box-sizing: border-box; margin: 0; padding: 0; }
  html, body { width: 1200px; height: 703px; overflow: hidden; }
  body {
    background: var(--backdrop);
    font-family: "Lato", sans-serif;
    position: relative;
  }

  /* ---------- Letterhead ---------- */
  .letter {
    position: absolute;
    left: 52px; top: 56px;
    width: 428px; height: 602px;
    background: linear-gradient(165deg, var(--paper) 20%, var(--paper-shade) 100%);
    border: 1px solid #d5d6da;
  }
  .brand {
    position: absolute;
    display: flex; align-items: center; gap: 8px;
  }
  .brand-mark { background: var(--navy); }
  .brand-name {
    font-family: "Lato", sans-serif;
    font-weight: 700;
    color: var(--navy);
    letter-spacing: 0.5px;
  }
  .letter .brand { left: 25px; top: 14px; }
  .letter .brand-mark { width: 34px; height: 34px; }
  .letter .brand-name { font-size: 30px; }

  .web-rule {
    position: absolute;
    display: flex; align-items: center;
  }
  .web-rule .rule { height: 2px; background: var(--steel-line); }
  .web-rule .web {
    font-size: 11px; letter-spacing: 2px; color: #3a3b40;
    white-space: nowrap;
  }
  .web-rule .web b { font-weight: 400; color: var(--steel); }

  .letter .web-rule { left: 0; top: 63px; width: 428px; }
  .letter .web-rule .rule:first-child { width: 298px; }
  .letter .web-rule .web { padding: 0 9px 0 10px; }
  .letter .web-rule .rule:last-child { flex: 1; }

  .letter-body {
    position: absolute;
    left: 25px; top: 98px; width: 385px;
  }
  .letter-body .paragraph {
    font-size: 8.1px; line-height: 13px; color: var(--body-text);
    text-align: justify;
    margin-bottom: 11px;
  }
  .letter-body .salutation {
    font-size: 11px; line-height: 14px; font-weight: 700; color: var(--navy);
    margin-bottom: 8px;
  }
  .letter-body .closing {
    margin-top: 25px;
    font-size: 12px; line-height: 15px; color: #4a4b50;
  }
  .letter-body .signature {
    font-family: "Yellowtail", cursive;
    font-size: 24px; line-height: 28px; color: var(--navy);
    margin-top: 0;
  }

  .contact-bar {
    position: absolute;
    left: 0; right: 0; top: 582px;
    display: flex; justify-content: center; align-items: center;
    font-size: 8px; color: #3c3d42;
  }
  .contact-item { display: flex; align-items: center; gap: 3px; padding: 0 10px; }
  .contact-item + .contact-item { border-left: 1px solid #b7b9c0; }
  .contact-item svg { width: 8px; height: 8px; }

  /* ---------- Envelope ---------- */
  .envelope-flap {
    position: absolute;
    left: 534px; top: 88px;
    width: 604px; height: 109px;
  }
  .envelope {
    position: absolute;
    left: 534px; top: 196px;
    width: 603px; height: 428px;
    background: var(--paper);
  }
  .envelope .brand { left: 30px; top: 27px; }
  .envelope .brand-mark { width: 42px; height: 42px; }
  .envelope .brand-name { font-size: 36px; }

  .envelope .web-rule { left: 0; top: 402px; width: 603px; }
  .envelope .web-rule .rule { flex: 1; }
  .envelope .web-rule .web { padding: 0 12px 0 11px; font-size: 11.5px; }
</style>
</head>
<body>

  <!-- Letterhead -->
  <article class="letter">
    <div class="brand">
      <span class="brand-mark"></span>
      <span class="brand-name">TaVRin</span>
    </div>

    <div class="web-rule">
      <span class="rule"></span>
      <span class="web">www.<b>tavrin</b>.ch</span>
      <span class="rule"></span>
    </div>

    <div class="letter-body">
      <p class="salutation">Dear Mr. Lorem,</p>
      <p class="paragraph">Lorem ipsum dolor sit amet, consectetuer adipiscing elit, sed diam nonummy nibh euismod tincidunt ut laoreet dolore magna aliquam erat volutpat. Ut wisi enim ad minim veniam, quis nostrud exerci tation ullamcorper suscipit lobortis nisl ut aliquip ex ea commodo consequat. Duis autem vel eum iriure dolor in hendiusto odio dignissim qui blandit praesent luptatum zzril delenit.facilisi.</p>
      <p class="paragraph">Lorem ipsum dolor sit amet, consectetuer adipiscing elit, sed diam nonummy nibh euismod tincidunt ut laoreet dolore magna aliquam erat volutpat. Ut wisi enim ad minim veniam, quis nostrud exerci tation ullamcorper suscipit lobortis nisl ut aliquip ex ea commodo consequat.</p>
      <p class="paragraph">Lorem ipsum dolor sit amet, consectetuer adipiscing elit, sed diam nonummy nibh euismod tincidunt ut laoreet dolore magna aliquam erat volutpat. Ut wisi enim ad minim veniam, quis nostrud exerci tation ullamcorper suscipit lobortis nisl ut aliquip ex ea commodo consequat. Duis autem vel eum iriure dolor in hendiusto odio dignissim qui blandit praesent luptatum zzril delenit.facilisi.</p>
      <p class="paragraph">Lorem ipsum dolor sit amet, consectetuer adipiscing elit, sed diam nonummy nibh euismod tincidunt ut laoreet dolore magna aliquam erat volutpat. Ut wisi enim ad minim veniam, quis nostrud exerci tation ullamcorper suscipit lobortis nisl ut aliquip ex ea commodo consequat.</p>
      <p class="paragraph">Lorem ipsum dolor sit amet, consectetuer adipiscing elit, sed diam nonummy nibh euismod tincidunt ut laoreet dolore magna aliquam erat volutpat. Ut wisi enim ad minim veniam, quis nostrud exerci tation ullamcorper suscipit lobortis nisl ut aliquip ex ea commodo consequat. Duis autem vel eum iriure dolor in hendiusto odio dignissim qui blandit praesent luptatum zzril delenit.facilisi.</p>
      <p class="paragraph">Lorem ipsum dolor sit amet, consectetuer adipiscing elit, sed diam nonummy nibh euismod tincidunt ut laoreet dolore magna aliquam erat volutpat. Ut wisi enim ad minim veniam, quis nostrud exerci tation ullamcorper suscipit lobortis nisl ut aliquip ex ea commodo consequat.</p>
      <p class="closing">Sincerely Your,</p>
      <p class="signature">Your Name</p>
    </div>

    <footer class="contact-bar">
      <span class="contact-item">
        <svg viewBox="0 0 10 10" aria-hidden="true"><circle cx="5" cy="5" r="4.3" fill="none" stroke="#3c3d42" stroke-width="0.9"/><path d="M5 2.3a1.8 1.8 0 0 1 1.8 1.8C6.8 5.4 5 7.6 5 7.6S3.2 5.4 3.2 4.1A1.8 1.8 0 0 1 5 2.3z" fill="#3c3d42"/></svg>
        Lindmattstr. 4 9517 Rosswil
      </span>
      <span class="contact-item">
        <svg viewBox="0 0 10 10" aria-hidden="true"><circle cx="5" cy="5" r="4.3" fill="none" stroke="#3c3d42" stroke-width="0.9"/><path d="M3.4 2.6l1 1.2-.5.6c.3.7.8 1.2 1.5 1.5l.6-.5 1.2 1-.6.9C4.9 7.2 2.9 5.2 2.6 3.2z" fill="#3c3d42"/></svg>
        +41 71 555 02 48
      </span>
      <span class="contact-item">
        <svg viewBox="0 0 10 10" aria-hidden="true"><rect x="1" y="2.5" width="8" height="5.5" fill="#3c3d42"/><path d="M1 2.5l4 3 4-3" fill="none" stroke="#fff" stroke-width="0.8"/></svg>
        info@tavrin.ch
      </span>
    </footer>
  </article>

  <!-- Envelope -->
  <svg class="envelope-flap" viewBox="0 0 604 109" aria-hidden="true">
    <path d="M0 109 L10 62 Q16 44 46 38 L262 4 Q298 -2 334 4 L556 38 Q586 44 592 62 L604 109 Z" fill="#7e9bb4"/>
  </svg>
  <section class="envelope">
    <div class="brand">
      <span class="brand-mark"></span>
      <span class="brand-name">TaVrn</span>
    </div>
    <div class="web-rule">
      <span class="rule"></span>
      <span class="web">www.<b>tavrin</b>.ch</span>
      <span class="rule"></span>
    </div>
  </section>

</body>
</html>
```